Tellmora Corporate Stationery

Look for design of all new corporate stationery for an existing insurance broking business that is going through a redesign and move from older partners to younger family members. New Logo is attached. Company is Brisbane based.
Colours in the Logo is Hex #43bed8 and website features a lot of hex #17b8d8. Website front page "A plan to protect you" - headline. "Professional and Individual advice to protect your greatest assets" - tagline.

Stationery required: Business Cards, Letter head, Thank-you cards, Birthday cards, Presentation folders, With Compliment slips and a powerpoint template. We also would like to send a card to all customers with the something along of the lines of "something new".

Target Market(s)

Customers of Insurance business looking at superannuation, life and income protection insurance, investment advice and wills

Industry/Entity Type

Insurance Broker

Font styles to use
Other font styles liked:
• same as logo

Requirements
Must have
• The above designs for new stationery for the new business including:
• Business Cards, Letter head, Thank-you cards, Birthday cards, Presentation folders, With Compliment slips and a powerpoint template. We also would like to send a card to all customers with the something along of the lines of "something new".
Nice to have
• It is a new look - long time family business being passed to next generation - big focus on advice for YOU, individual advice etc..

```html
<!DOCTYPE html>
<html lang="en">
<head>
<meta charset="utf-8">
<title>Tellmora Financial Group – Stationery</title>
<link href="https://fonts.googleapis.com/css2?family=Open+Sans:wght@400;600;700&display=swap" rel="stylesheet">
<style>
  :root{
    --brand:#43bed8;
    --brand-deep:#17b8d8;
    --navy:#163a4a;
    --ink:#2b2f33;
    --grey:#6d7175;
    --paper:#ffffff;
    --paper-tint:#f6f7f8;
    --backdrop:#e6e8eb;
  }
  *{box-sizing:border-box;margin:0;padding:0}
  html,body{width:1200px;height:1200px;overflow:hidden}
  body{background:var(--backdrop);font-family:"Open Sans",Arial,sans-serif;color:var(--ink);position:relative}
  .sheet{position:absolute;background:linear-gradient(135deg,var(--paper) 0%,var(--paper-tint) 100%);box-shadow:0 6px 18px rgba(0,0,0,.14);overflow:hidden}

  .brand-name{font-weight:700;color:var(--brand);text-transform:uppercase;letter-spacing:.04em;line-height:1.05;display:flex;align-items:center;gap:8px}
  .brand-name .dot{display:inline-block;border-radius:50%;background:var(--brand);flex:none}
  .brand-name .lines span{display:block;white-space:nowrap}

  .icon{display:inline-block;width:10px;height:10px;flex:none}
  .contact-row{display:flex;align-items:center;gap:6px;white-space:nowrap}

  .licence-band{position:absolute;right:0;background:var(--brand);color:var(--navy);font-weight:700;display:flex;align-items:center;white-space:nowrap;border-top:2px solid var(--paper);box-shadow:0 -2px 0 var(--navy)}

  /* business card – front */
  .card-front{left:60px;top:204px;width:430px;height:246px}
  .card-front .holder{position:absolute;right:28px;top:24px;text-align:right}
  .card-front .holder-name{color:var(--brand);font-weight:700;font-size:16px;letter-spacing:.02em}
  .card-front .holder-role{color:var(--grey);font-size:10.5px}
  .card-front .brand-name{position:absolute;left:22px;top:112px;font-size:16px}
  .card-front .brand-name .dot{width:10px;height:10px}
  .card-front .contacts{position:absolute;left:205px;top:86px;font-size:10px;color:var(--grey);display:flex;flex-direction:column;gap:6px}
  .card-front .licence-band{left:140px;bottom:26px;height:20px;font-size:7.5px;padding-left:10px}

  /* business card – back */
  .card-back{left:60px;top:474px;width:430px;height:246px;display:flex;align-items:center;justify-content:center}
  .card-back .brand-name{font-size:30px}
  .card-back .brand-name .dot{width:16px;height:16px}

  /* compliment slip */
  .slip{left:60px;top:760px;width:460px;height:217px}
  .slip .brand-name{position:absolute;left:26px;top:28px;font-size:18px}
  .slip .brand-name .dot{width:11px;height:11px}
  .slip .slip-title{position:absolute;right:26px;top:88px;color:var(--brand);font-weight:700;font-size:18px;letter-spacing:.3em}
  .slip .contacts{position:absolute;right:26px;top:122px;font-size:9.5px;color:var(--grey);display:grid;grid-template-columns:auto auto;gap:5px 14px}
  .slip .licence-band{left:96px;bottom:24px;height:22px;font-size:9.5px;padding-left:12px}

  /* letterhead */
  .letterhead{left:580px;top:204px;width:560px;height:792px}
  .letterhead .brand-name{position:absolute;left:48px;top:48px;font-size:24px}
  .letterhead .brand-name .dot{width:14px;height:14px}
  .letterhead .body-copy{position:absolute;left:48px;right:48px;top:150px;font-size:12px;line-height:1.65;color:var(--ink);display:flex;flex-direction:column;gap:16px;text-align:justify}
  .letterhead .contacts{position:absolute;right:36px;bottom:74px;font-size:11px;color:var(--grey);display:grid;grid-template-columns:auto auto;gap:6px 18px}
  .letterhead .licence-band{left:120px;bottom:30px;height:28px;font-size:12px;padding-left:14px}
</style>
</head>
<body>

<svg width="0" height="0" style="position:absolute" aria-hidden="true">
  <defs>
    <symbol id="icon-phone" viewBox="0 0 10 10"><rect width="10" height="10" rx="1.5" fill="#43bed8"/><path d="M3 2.2h1.2l.5 1.6-.8.6a4 4 0 0 0 1.8 1.8l.6-.8 1.6.5V7a.8.8 0 0 1-.8.8A5 5 0 0 1 2.2 3 .8.8 0 0 1 3 2.2z" fill="#fff"/></symbol>
    <symbol id="icon-web" viewBox="0 0 10 10"><rect width="10" height="10" rx="1.5" fill="#43bed8"/><circle cx="5" cy="5" r="2.8" fill="none" stroke="#fff" stroke-width=".8"/><path d="M2.2 5h5.6M5 2.2v5.6" stroke="#fff" stroke-width=".7"/></symbol>
    <symbol id="icon-mail" viewBox="0 0 10 10"><rect width="10" height="10" rx="1.5" fill="#43bed8"/><rect x="2" y="3" width="6" height="4" fill="none" stroke="#fff" stroke-width=".8"/><path d="M2 3l3 2.3L8 3" fill="none" stroke="#fff" stroke-width=".8"/></symbol>
    <symbol id="icon-pin" viewBox="0 0 10 10"><rect width="10" height="10" rx="1.5" fill="#43bed8"/><path d="M5 8.3S2.7 5.8 2.7 4.2a2.3 2.3 0 0 1 4.6 0C7.3 5.8 5 8.3 5 8.3z" fill="#fff"/><circle cx="5" cy="4.2" r=".8" fill="#43bed8"/></symbol>
  </defs>
</svg>

<section class="sheet card-front">
  <div class="holder">
    <div class="holder-name">ALEX MORGAN</div>
    <div class="holder-role">Director</div>
  </div>
  <div class="brand-name"><span class="dot"></span><span class="lines"><span>Tellmora</span><span>Financial Group</span></span></div>
  <div class="contacts">
    <div class="contact-row"><svg class="icon"><use href="#icon-phone"/></svg>1-234-555010</div>
    <div class="contact-row"><svg class="icon"><use href="#icon-web"/></svg>www.tellmorafinancial.com</div>
    <div class="contact-row"><svg class="icon"><use href="#icon-mail"/></svg>john@tellmorafinancial.com</div>
    <div class="contact-row"><svg class="icon"><use href="#icon-pin"/></svg>Dummy city, Dummy Country Land</div>
  </div>
  <div class="licence-band">Authorised Representatives of Verando AFS Licence No 518204</div>
</section>

<section class="sheet card-back">
  <div class="brand-name"><span class="dot"></span><span class="lines"><span>Tellmora</span><span>Financial Group</span></span></div>
</section>

<section class="sheet slip">
  <div class="brand-name"><span class="dot"></span><span class="lines"><span>Tellmora</span><span>Financial Group</span></span></div>
  <div class="slip-title">WITH COMPLIMENT</div>
  <div class="contacts">
    <div class="contact-row">www.tellmorafinancial.com<svg class="icon"><use href="#icon-web"/></svg></div>
    <div class="contact-row"><svg class="icon"><use href="#icon-phone"/></svg>1-234-555010</div>
    <div class="contact-row">Dummy city, Dummy Country Land<svg class="icon"><use href="#icon-pin"/></svg></div>
    <div class="contact-row"><svg class="icon"><use href="#icon-mail"/></svg>john@tellmorafinancial.com</div>
  </div>
  <div class="licence-band">Authorised Representatives of Verando AFS Licence No 518204</div>
</section>

<section class="sheet letterhead">
  <div class="brand-name"><span class="dot"></span><span class="lines"><span>Tellmora</span><span>Financial Group</span></span></div>
  <div class="body-copy">
    <p>Lorem ipsum dolor sit amet, consectetur adipiscing elit. Sed at ante. Mauris eleifend, quam a vulputate dictum, massa quam dapibus leo, eget vulputate orci purus ut lorem. In fringilla mi in ligula. Pellentesque aliquam quam vel dolor. Nunc adipiscing. Sed quam odio, tempus ac, aliquam molestie, varius ac, tellus. Vestibulum ut nulla aliquam risus rutrum interdum. Pellentesque lorem.</p>
    <p>Curabitur sit amet erat quis risus feugiat viverra. Pellentesque augue justo, sagittis et, lacinia at, venenatis non, arcu. Nunc nec libero. In cursus dictum risus. Etiam tristique nisl a nulla. Ut a orci. Curabitur dolor nunc, egestas at, accumsan at, malesuada nec, magna. Nulla facilisi. Nunc volutpat. Vestibulum ante ipsum primis in faucibus orci luctus et ultrices posuere cubilia Curae; Ut sit amet orci vel mauris blandit vehicula. Nullam quis enim. Integer dignissim viverra velit. Curabitur in odio.</p>
    <p>In consequat, tellus eu volutpat varius, justo orci elementum diam. Vestibulum ipsum ante, malesuada quis, tempus ac, placerat sit amet, elit. Pellentesque augue justo, sagittis et, lacinia at, venenatis non, arcu. Etiam tristique nisl a nulla. Ut a orci. Nulla facilisi. Nunc volutpat. Vestibulum ante ipsum primis in faucibus orci luctus et ultrices posuere cubilia Curae; Nullam quis enim. Integer dignissim viverra velit.</p>
  </div>
  <div class="contacts">
    <div class="contact-row">www.tellmorafinancial.com<svg class="icon"><use href="#icon-web"/></svg></div>
    <div class="contact-row"><svg class="icon"><use href="#icon-phone"/></svg>1-234-555010</div>
    <div class="contact-row">Dummy city, Dummy Country Land<svg class="icon"><use href="#icon-pin"/></svg></div>
    <div class="contact-row"><svg class="icon"><use href="#icon-mail"/></svg>john@tellmorafinancial.com</div>
  </div>
  <div class="licence-band">Authorised Representatives of Verando AFS Licence No 518204</div>
</section>

</body>
</html>
```